Design concept Visual UI of future mobile app - healthcare

Hi,
I'm looking for a top designer, innovative with strong experience in user interface

The app will be connected to a future health website related to depression and addiction by helping the user to track the moods, tired, anxiety using this mobile app.

I attached the deck of the overall project but I can send you a specific presentation for the app only

thanks

Target Market(s)

Switzerland, UK, Germany and France

Industry/Entity Type

Mental Health

Logo Text

Health, hope

Font styles to use
Sans Serif

Colors
cee9f5
33a6d7
0692cd
0255a3
3276b5
85abd2

Requirements
Must have
• keep it simple, easy to navigate
• The user should be able to track the moods on a daily basis,
• sleep time, and rate how the feel on the day
• To be able to get information from the sync deck of vexlo
Nice to have
• to be able share this app with a friend

```html
<!DOCTYPE html>
<html lang="en">
<head>
<meta charset="utf-8">
<title>Tracking Graphs</title>
<link rel="stylesheet" href="https://fonts.googleapis.com/css2?family=Roboto:wght@400;500;700&display=swap">
<style>
  :root {
    --page-bg: #ecebe7;
    --sky-top: #0692cd;
    --sky-mid: #33a6d7;
    --sky-low: #85abd2;
    --sky-pale: #cee9f5;
    --ink-light: #ffffff;
    --ink-soft: rgba(255,255,255,0.85);
    --label: #e6f3fa;
  }
  * { box-sizing: border-box; margin: 0; padding: 0; }
  html, body { width: 1200px; height: 800px; overflow: hidden; }
  body {
    background: var(--page-bg);
    font-family: "Roboto", Arial, sans-serif;
    position: relative;
  }
  .app-screen {
    position: absolute;
    left: 400px; top: 44px;
    width: 400px; height: 712px;
    background: linear-gradient(180deg, var(--sky-top) 0%, var(--sky-mid) 35%, var(--sky-low) 75%, var(--sky-pale) 100%);
    color: var(--ink-light);
    overflow: hidden;
  }
  .status-bar {
    height: 22px; padding: 0 10px;
    display: flex; align-items: center; justify-content: space-between;
    font-size: 11px; font-weight: 500;
  }
  .status-bar .carrier { letter-spacing: 0.5px; }
  .app-header {
    height: 40px; padding: 0 14px;
    display: flex; align-items: center; gap: 10px;
  }
  .app-header .title {
    flex: 1; text-align: center;
    font-size: 17px; font-weight: 700; letter-spacing: 0.5px;
  }
  .section-label {
    text-align: center; font-size: 11px; font-weight: 700;
    letter-spacing: 0.6px; line-height: 1.2;
  }
  .chart { display: block; margin: 6px auto 0; }
  .axis-labels {
    width: 340px; margin: 4px auto 0;
    display: grid; grid-template-columns: repeat(12, 1fr);
    text-align: center; font-size: 9px; line-height: 1.25; color: var(--label);
  }
  .week-block { margin-top: 4px; }
  .month-block { margin-top: 14px; }
</style>
</head>
<body>
  <main class="app-screen">
    <div class="status-bar">
      <span class="carrier">●●●○○ TELRA</span>
      <span class="clock">4:21 PM</span>
      <span class="battery">100%</span>
    </div>

    <header class="app-header">
      <svg width="18" height="14" viewBox="0 0 18 14" aria-hidden="true"><g stroke="#fff" stroke-width="2"><line x1="0" y1="2" x2="18" y2="2"/><line x1="0" y1="7" x2="18" y2="7"/><line x1="0" y1="12" x2="18" y2="12"/></g></svg>
      <svg width="10" height="16" viewBox="0 0 10 16" aria-hidden="true"><polyline points="8,1 2,8 8,15" fill="none" stroke="#fff" stroke-width="1.6"/></svg>
      <h1 class="title">TRACKING GRAPHS</h1>
      <svg width="10" height="16" viewBox="0 0 10 16" aria-hidden="true"><polyline points="2,1 8,8 2,15" fill="none" stroke="#fff" stroke-width="1.6"/></svg>
    </header>

    <section class="week-block">
      <h2 class="section-label">WEEK</h2>
      <svg class="chart week-chart" width="340" height="220" viewBox="0 0 340 220" role="img" aria-label="Daily mood line chart over twelve days">
        <g class="bands">
          <rect y="0" width="340" height="22" fill="#e2231a"/>
          <rect y="22" width="340" height="22" fill="#ea4a1e"/>
          <rect y="44" width="340" height="22" fill="#f07a22"/>
          <rect y="66" width="340" height="22" fill="#f3a527"/>
          <rect y="88" width="340" height="22" fill="#e3bf2c"/>
          <rect y="110" width="340" height="22" fill="#c2b835"/>
          <rect y="132" width="340" height="22" fill="#a7ab3a"/>
          <rect y="154" width="340" height="22" fill="#959f3f"/>
          <rect y="176" width="340" height="22" fill="#8a8f49"/>
          <rect y="198" width="340" height="22" fill="#847d5e"/>
        </g>
        <g class="grid" stroke="rgba(255,255,255,0.35)" stroke-width="1">
          <line x1="28" y1="0" x2="28" y2="220"/><line x1="57" y1="0" x2="57" y2="220"/>
          <line x1="85" y1="0" x2="85" y2="220"/><line x1="113" y1="0" x2="113" y2="220"/>
          <line x1="142" y1="0" x2="142" y2="220"/><line x1="170" y1="0" x2="170" y2="220"/>
          <line x1="198" y1="0" x2="198" y2="220"/><line x1="227" y1="0" x2="227" y2="220"/>
          <line x1="255" y1="0" x2="255" y2="220"/><line x1="283" y1="0" x2="283" y2="220"/>
          <line x1="312" y1="0" x2="312" y2="220"/>
        </g>
        <polyline fill="none" stroke="#fff" stroke-width="1.5"
          points="14,143 42,154 70,77 99,55 127,88 156,99 184,72 213,55 241,62 269,10 298,99 326,106"/>
        <g fill="#fff">
          <circle cx="14" cy="143" r="3.5"/><circle cx="42" cy="154" r="3.5"/>
          <circle cx="70" cy="77" r="3.5"/><circle cx="99" cy="55" r="3.5"/>
          <circle cx="127" cy="88" r="3.5"/><circle cx="156" cy="99" r="3.5"/>
          <circle cx="184" cy="72" r="3.5"/><circle cx="213" cy="55" r="3.5"/>
          <circle cx="241" cy="62" r="3.5"/><circle cx="269" cy="10" r="3.5"/>
          <circle cx="298" cy="99" r="3.5"/><circle cx="326" cy="106" r="3.5"/>
        </g>
      </svg>
      <div class="axis-labels">
        <span>Mon<br>21/5</span><span>Tue<br>22/5</span><span>Wed<br>23/5</span><span>Thu<br>24/5</span>
        <span>Fri<br>25/5</span><span>Sat<br>26/5</span><span>Sun<br>27/5</span><span>Mon<br>28/5</span>
        <span>Tue<br>29/5</span><span>Wed<br>30/5</span><span>Thu<br>31/5</span><span>Fri<br>1/6</span>
      </div>
    </section>

    <section class="month-block">
      <h2 class="section-label">MONTH<br>2015</h2>
      <svg class="chart month-chart" width="340" height="250" viewBox="0 0 340 250" role="img" aria-label="Monthly mood line chart with trend line for 2015">
        <defs>
          <linearGradient id="month-heat" x1="0" y1="0" x2="0" y2="1">
            <stop offset="0" stop-color="#e8281c"/>
            <stop offset="0.2" stop-color="#f07524"/>
            <stop offset="0.4" stop-color="#eebb2a"/>
            <stop offset="0.6" stop-color="#a9ab3a"/>
            <stop offset="0.85" stop-color="#8d9246"/>
            <stop offset="1" stop-color="#847d5e"/>
          </linearGradient>
        </defs>
        <rect width="340" height="250" fill="url(#month-heat)"/>
        <g class="grid" stroke="rgba(255,255,255,0.5)" stroke-width="1">
          <line x1="28" y1="0" x2="28" y2="250"/><line x1="57" y1="0" x2="57" y2="250"/>
          <line x1="85" y1="0" x2="85" y2="250"/><line x1="113" y1="0" x2="113" y2="250"/>
          <line x1="142" y1="0" x2="142" y2="250"/><line x1="170" y1="0" x2="170" y2="250"/>
          <line x1="198" y1="0" x2="198" y2="250"/><line x1="227" y1="0" x2="227" y2="250"/>
          <line x1="255" y1="0" x2="255" y2="250"/><line x1="283" y1="0" x2="283" y2="250"/>
          <line x1="312" y1="0" x2="312" y2="250"/>
        </g>
        <line x1="0" y1="205" x2="340" y2="95" stroke="#fff" stroke-width="1.5"/>
        <polyline fill="none" stroke="#fff" stroke-width="1.5"
          points="0,205 14,190 28,160 42,130 57,150 70,125 85,118 99,135 113,128 127,110 142,138 156,120 170,105 184,118 198,100 212,92 227,110 241,85 255,60 269,72 283,55 298,70 312,45 326,40 340,30"/>
      </svg>
      <div class="axis-labels">
        <span>Jan</span><span>Feb</span><span>Mar</span><span>Apr</span><span>May</span><span>Jun</span>
        <span>Jul</span><span>Aug</span><span>Sep</span><span>Oct</span><span>Nov</span><span>Dec</span>
      </div>
    </section>
  </main>
</body>
</html>
```